Cat-products company needs smart, yet endearing, business card

We need a business card design for a new, but up-and-running, business based in Honolulu, Hawaii. The business is Purrnest Nook Co. Our first product is the most environmentally-friendly cat grass kit ever seen on the planet. Future products, currently in the R&D phase, will include a variety of exciting cat scratchers. We also do consulting work to help apartment-dwellers make their home more cat-friendly and, in the future, plan on doing full, custom installs of structure to create high walkways for cats.

Target Market(s)

Middle-aged, apartment-dwelling, middle-class workers who own 1 or more cats and who dote on them.

Industry/Entity Type

Pet Care

Contact Information for Business Card

A striking, professional, yet warm and friendly design is what we're after.

Font styles to use
Serif
Sans Serif
Other font styles liked:
• Comfortaa

Colors

Designer to choose colors to be used in the design.

Requirements
Must have
• The company logo: (see attachment)
• The company name: Purrnest Nook Co
• The web address: www.purrnestnookco.com
• Email: support@purrnestnookco.com
• Phone: +1 (808) 571 6023
• Update (Fri Jun 30 3017 7:45pm Hawaii Time) I would like, is possible, uploaded picture of the cat grass kit on the back of the card with some text along the lines of: Purrnest Nook Co - Maker Of The Leafiest Feline Sprout Set Yet
Nice to have
• A cat picture, cartoon, real or silhouette that illustrates cats in action and/or relaxing; ie using the apartment space to live, play and relax in and being well-contented.
• Most of the website is done in the font: Comfortaa. It might be nice to continue using this for brand consistency.
Should not have
• Hard-to-read fonts.

```html
<!DOCTYPE html>
<html lang="en">
<head>
<meta charset="utf-8">
<title>Purrnest Nook Co – Business Card</title>
<link href="https://fonts.googleapis.com/css2?family=Jost:wght@400;500;600&display=swap" rel="stylesheet">
<style>
  :root {
    --backdrop: #2b2b2d;
    --card-white: #f7f7f5;
    --card-dark: #2a292b;
    --brand-yellow: #f2bb17;
    --brand-brown: #7a4a3a;
    --text-grey: #8d8d8d;
    --text-light: #e6e6e6;
    --blue-deep: #1c4fa8;
    --blue-bright: #2a8fd0;
  }
  * { box-sizing: border-box; margin: 0; padding: 0; }
  html, body { width: 1200px; height: 1000px; overflow: hidden; }
  body {
    background: var(--backdrop);
    font-family: "Jost", sans-serif;
    display: flex;
    flex-direction: column;
    align-items: center;
    justify-content: center;
    gap: 60px;
  }
  .card {
    width: 700px;
    height: 400px;
    position: relative;
    overflow: hidden;
    box-shadow: 0 12px 30px rgba(0,0,0,0.45);
  }

  /* Front */
  .card-front { background: var(--card-white); }
  .front-upper {
    position: absolute; left: 0; top: 0; right: 0; height: 248px;
    background: var(--card-white);
  }
  .divider {
    position: absolute; left: 0; right: 0; top: 248px; height: 4px;
    background: var(--brand-yellow);
  }
  .front-lower {
    position: absolute; left: 0; right: 0; top: 252px; bottom: 0;
    background: var(--card-dark);
  }
  .person {
    position: absolute; top: 36px; right: 40px;
    display: flex; align-items: stretch; gap: 14px;
    text-align: right;
  }
  .person-name {
    color: var(--brand-yellow); font-weight: 600; font-size: 22px;
    letter-spacing: 1px; text-transform: uppercase; line-height: 1.1;
  }
  .person-role { color: var(--text-grey); font-size: 16px; margin-top: 4px; }
  .person-bar { width: 6px; background: #9a9a9a; }

  .brand-mark {
    display: flex; align-items: center; gap: 12px;
  }
  .brand-square { width: 34px; height: 34px; background: var(--brand-brown); }
  .brand-name {
    color: var(--brand-yellow); font-weight: 600; font-size: 30px; line-height: 1;
  }
  .front-brand { position: absolute; left: 40px; bottom: 190px; }

  .contact-list {
    position: absolute; left: 40px; top: 34px;
    list-style: none; display: flex; flex-direction: column; gap: 10px;
  }
  .contact-item {
    display: flex; align-items: center; gap: 14px;
    color: var(--text-light); font-size: 17px;
  }
  .contact-item svg { width: 16px; height: 16px; fill: var(--brand-yellow); }
  .accent { color: var(--brand-yellow); }

  .address {
    position: absolute; right: 40px; top: 34px;
    color: var(--text-light); font-size: 17px; line-height: 1.5; text-align: right;
  }

  /* Back */
  .card-back {
    background: radial-gradient(ellipse at 45% 40%, var(--blue-bright) 0%, var(--blue-deep) 75%);
    display: flex; align-items: center; justify-content: center;
  }
  .card-back .brand-square { width: 52px; height: 52px; }
  .card-back .brand-name { font-size: 46px; }
</style>
</head>
<body>

  <section class="card card-front" aria-label="Business card front">
    <div class="front-upper">
      <div class="person">
        <div>
          <p class="person-name">Dana Whitfield</p>
          <p class="person-role">Director</p>
        </div>
        <span class="person-bar"></span>
      </div>
    </div>
    <div class="brand-mark front-brand">
      <span class="brand-square"></span>
      <span class="brand-name">Purrnest Nook Co</span>
    </div>
    <div class="divider"></div>
    <div class="front-lower">
      <ul class="contact-list">
        <li class="contact-item">
          <svg viewBox="0 0 16 16" aria-hidden="true"><path d="M3.5 1.5l2.5 0 1 3.5-1.6 1.2a8 8 0 0 0 4.4 4.4l1.2-1.6 3.5 1v2.5c0 .8-.7 1.5-1.5 1.5A12.5 12.5 0 0 1 2 3c0-.8.7-1.5 1.5-1.5z"/></svg>
          <span>+1 (808) 571 6023</span>
        </li>
        <li class="contact-item">
          <svg viewBox="0 0 16 16" aria-hidden="true"><path d="M1 3h14v10H1z M2 4l6 5 6-5" fill="none" stroke="var(--brand-yellow)" stroke-width="1.6"/></svg>
          <span>support@purrnestnookco.com</span>
        </li>
        <li class="contact-item">
          <svg viewBox="0 0 16 16" aria-hidden="true"><circle cx="8" cy="8" r="6.5" fill="none" stroke="var(--brand-yellow)" stroke-width="1.5"/><path d="M1.5 8h13M8 1.5c-3 3.5-3 9.5 0 13M8 1.5c3 3.5 3 9.5 0 13" fill="none" stroke="var(--brand-yellow)" stroke-width="1.2"/></svg>
          <span>www.<span class="accent">purrnestnookco</span>.com</span>
        </li>
      </ul>
      <p class="address">48 Kiawe Lane,<br>Honolulu, 96815</p>
    </div>
  </section>

  <section class="card card-back" aria-label="Business card back">
    <div class="brand-mark">
      <span class="brand-square"></span>
      <span class="brand-name">Purrnest Nook Co</span>
    </div>
  </section>

</body>
</html>
```